I need a book cover (front and back) for a book I wrote called "7 Laws of Polish: A Closet Map for Triumph".

The short version of the book can be found online here: https://filebin.example.net/file/d/7KqPzR2mXwT9bLcN4vHs8YdJ3fGeA0uWi/view

I'm working on expanding this into a real book (100+ pages, with images), and putting it on Pellora.

I'm the author, Joel Mackworth. I was named "Sharpest Gent of the Nation" by Dapperly Journal, and I would like to add that to the cover for credibility.

My website "About Page" has more info about me and my business Threadwell House: https://threadwellhouse.example/pages/about-us

I also attached the first version of the cover I made using Canva.

I have LOTS of images, if you need some (mannequins, models, garments, etc). See our website's blog for more ideas of the images we have: https://threadwellhouse.example/blogs/news

```html
<!DOCTYPE html>
<html lang="en">
<head>
<meta charset="utf-8">
<title>7 Laws of Polish — Book Cover</title>
<link rel="stylesheet" href="https://fonts.googleapis.com/css2?family=DM+Serif+Display&family=Questrial&family=Montserrat:wght@700&display=swap">
<style>
  :root {
    --ink: #050505;
    --gold: #b9a57a;
    --cream: #efece3;
    --white: #ffffff;
    --photo-dark: #14100d;
    --photo-warm: #3a2c22;
    --portrait-tone: #3b3d42;
  }
  * { margin: 0; padding: 0; box-sizing: border-box; }
  html, body { width: 1200px; height: 890px; overflow: hidden; background: var(--ink); }
  .cover { position: relative; width: 1200px; height: 890px; background: var(--ink); color: var(--white); font-family: "Questrial", sans-serif; }

  .serif { font-family: "DM Serif Display", serif; }

  /* Back cover */
  .back-mark { position: absolute; left: 100px; top: 105px; width: 95px; height: 150px; }
  .back-pitch { position: absolute; left: 102px; top: 116px; width: 400px; font-size: 10.2px; line-height: 12.9px; }
  .back-pitch h2 { font-family: "Questrial", sans-serif; color: var(--gold); font-size: 13.5px; font-weight: 700; letter-spacing: 0.01em; margin: 0 0 4px 91px; -webkit-text-stroke: 0.3px var(--gold); }
  .back-pitch p { text-align: justify; margin-bottom: 4.5px; }
  .back-pitch .indent { margin-left: 91px; }
  .back-pitch .closing { text-align: left; margin-bottom: 0; }
  .signature { display: inline-flex; align-items: center; gap: 6px; }
  .signature::after { content: ""; display: inline-block; width: 5px; height: 13px; background: var(--gold); margin-left: 6px; }

  .author-portrait { position: absolute; left: 217px; top: 333px; width: 166px; height: 166px; border-radius: 50%; border: 1px solid var(--gold); padding: 5px; }
  .author-portrait .photo { width: 100%; height: 100%; border-radius: 50%; background: radial-gradient(circle at 50% 40%, #55565b, var(--portrait-tone) 55%, #1e1f24); }

  .bio { position: absolute; left: 102px; top: 522px; width: 401px; font-size: 10.3px; line-height: 12.9px; }
  .bio p { text-align: justify; margin-bottom: 4.3px; }
  .bio .visit { font-size: 12.3px; margin-top: 6px; text-align: left; }
  .bio .visit a { color: var(--gold); text-decoration: none; }

  .barcode-area { position: absolute; left: 372px; top: 738px; width: 192px; height: 115px; background: var(--white); }

  /* Spine */
  .spine-title, .spine-author { position: absolute; writing-mode: vertical-rl; color: var(--cream); }
  .spine-title { left: 591px; top: 60px; font-family: "DM Serif Display", serif; font-size: 8.5px; }
  .spine-author { left: 593px; top: 764px; font-family: "Montserrat", sans-serif; font-weight: 700; font-size: 6.6px; letter-spacing: 0.18em; }

  /* Front cover */
  .front-photo { position: absolute; left: 611px; top: 0; width: 589px; height: 890px;
    background:
      radial-gradient(ellipse 60% 22% at 85% 78%, rgba(214,190,150,0.45), transparent 70%),
      radial-gradient(ellipse 40% 45% at 50% 55%, rgba(40,60,110,0.45), transparent 75%),
      linear-gradient(180deg, #120f0d 0%, var(--photo-warm) 45%, #2a2018 70%, var(--photo-dark) 100%); }
  .front-type { position: absolute; left: 611px; top: 0; width: 589px; height: 890px; }
  .front-type .accolade { font-family: "Questrial", sans-serif; font-size: 12.6px; fill: var(--white); }
  .front-type .rule { stroke: var(--cream); stroke-width: 0.8; }
  .front-type .numeral { fill: var(--gold); }
  .front-type .title-word { fill: var(--cream); }
  .front-type .author { font-family: "Montserrat", sans-serif; font-weight: 700; font-size: 22px; letter-spacing: 8px; fill: var(--white); }
  .back-mark .numeral { fill: var(--gold); }
  .back-mark .title-word { fill: var(--white); }
</style>
</head>
<body>
<main class="cover">

  <!-- Back cover -->
  <svg class="back-mark" viewBox="0 0 95 150" aria-label="7 Laws of Polish">
    <text class="serif numeral" x="45" y="81" font-size="102" text-anchor="middle">7</text>
    <text class="serif title-word" x="45" y="109" font-size="31" text-anchor="middle">Laws</text>
    <text class="serif title-word" x="45" y="121" font-size="16" text-anchor="middle">of</text>
    <text class="serif title-word" x="45" y="143" font-size="29" text-anchor="middle" textLength="82" lengthAdjust="spacingAndGlyphs">Polish</text>
  </svg>

  <section class="back-pitch">
    <h2>Style is not vanity. It's strategy.</h2>
    <p class="indent">Like it or not, the way you dress has a huge impact on your life. It doesn’t matter how smart you are or how good you are at your job, if people assume you are sloppy and can’t be trusted you’re fighting an uphill battle.</p>
    <p class="indent">The good news is, style - like any other skill - is something you can learn, practice and improve. This book will give you a foundation for understanding how to dress with style and build a lasting wardrobe that works for you.</p>
    <p><span style="padding-left:91px"></span>I’ve used these principles to help thousands of people get raises and promotions, meet their future partners, become the leader of their social circles and significantly improve their confidence.</p>
    <p class="closing">I hope it helps you become the best version of yourself and live your best life.<br><span class="signature">-Joel Mackworth</span></p>
  </section>

  <figure class="author-portrait">
    <div class="photo" role="img" aria-label="Portrait photograph of the author in a tweed jacket and tie"></div>
  </figure>

  <section class="bio">
    <p>Joel Mackworth was named “Sharpest Gent of the Nation” by Dapperly Journal while studying psychology at Halverton University. He then trained to become a bespoke tailor and earned a degree in menswear design from the Marlowe Institute of Design.</p>
    <p>After 10 years of doing custom tailoring for clients in New York City, Joel combined his experience in bespoke tailoring with his passion for teaching men how to dress for success and created Threadwell House; a full-service bespoke tailor shop online.</p>
    <p>Today Joel lives in Toronto with his wife Elise and their daughter Mira where he meets with customers on Meetly to refine their personal style and build their dream wardrobes.</p>
    <p class="visit">Visit <a href="https://threadwellhouse.example">www.threadwellhouse.example</a> for more information.</p>
  </section>

  <div class="barcode-area"></div>

  <!-- Spine -->
  <div class="spine-title">7 Laws <small style="font-size:4px">of</small> Polish</div>
  <div class="spine-author">JOEL MACKWORTH</div>

  <!-- Front cover -->
  <div class="front-photo" role="img" aria-label="Photograph of the author standing in a blue three-piece suit inside a dim brick warehouse with sunlight on the wooden floor"></div>

  <svg class="front-type" viewBox="0 0 589 890" aria-label="7 Laws of Polish by Joel Mackworth">
    <line class="rule" x1="191" y1="59" x2="382" y2="59"/>
    <text class="accolade" x="286" y="76" text-anchor="middle">“Sharpest Gent of the Nation” by Dapperly Journal</text>
    <line class="rule" x1="191" y1="84" x2="382" y2="84"/>

    <text class="serif numeral" x="284" y="433" font-size="460" text-anchor="middle">7</text>
    <text class="serif title-word" x="287" y="576" font-size="132" text-anchor="middle">Laws</text>
    <text class="serif title-word" x="290" y="634" font-size="72" text-anchor="middle">of</text>
    <text class="serif title-word" x="288" y="738" font-size="122" text-anchor="middle" textLength="360" lengthAdjust="spacingAndGlyphs">Polish</text>

    <text class="author" x="290" y="846" text-anchor="middle">JOEL MACKWORTH</text>
  </svg>

</main>
</body>
</html>
```